Bolts & Burdens: Mending What Lies Beneath

AUTHORS BIO:
Wade Pemberton is a 20-year Northern Union Aerial Corps veteran who served as a Crew Chief for K-37 and K-48 fighter jets, maintaining the backbone of America’s air superiority through multiple deployments to Afghanistan and other austere locations. Shaped by the loss of his father as a young adult and the lingering scars of childhood trauma, he confronts PTSD with the same tenacity he brought to the flightline. A survivor and advocate, he brings a raw, hard-earned perspective to "Bolts and Burdens," blending the grit of a serviceman with the insight of a man determined to heal. Focused on helping men confront their pain and find strength in vulnerability. Wade now lives in Jacksonville, North Carolina, where he continues to advocate for those shaped by trauma’s lasting weight.

SUMMARY:
In this raw and revealing non-fiction work, Wade Pemberton delves into the lasting echoes of childhood trauma and its profound impact on adult life, with a lens on his 20-year career in the Aerial Corps. Blending personal experience with hard-earned insight, the book explores how post-traumatic stress disorder (PTSD) shapes the mind and body, often in ways that remain hidden until the pressure builds beyond breaking points. With a focus on men—who are too often taught to bury their pain—this narrative offers a roadmap to understanding, confronting, and healing from the torque of trauma. Written in a direct, unflinching voice, "Bolts and Burdens" is both a memoir of resilience and a call to action for those ready to face the past to reclaim their future. Thank you for joining me on this adventure called life. It means more to me than you will ever know.

Target Market(s)

Those serving in the military and post military life with an emphasis on trauma

Font styles to use
Serif

Requirements
Must have
• NUAC K-37 or K-48 aircraft, NO AI GENERATED AIRCRAFT please
Nice to have
• An American Flag
Should not have
• AI generated aircraft

```html
<!DOCTYPE html>
<html lang="en">
<head>
<meta charset="utf-8">
<title>Bolts &amp; Burdens — Book Cover</title>
<link rel="stylesheet" href="https://fonts.googleapis.com/css2?family=Orbitron:wght@800&family=Outfit:wght@400;500&display=swap">
<style>
  :root {
    --page-bg: #ececec;
    --cover-white: #f7f7f7;
    --ink: #1f1a1b;
    --crimson: #b2384c;
    --slate: #66605a;
    --maroon: #3a171c;
  }
  * { margin: 0; padding: 0; box-sizing: border-box; }
  html, body { width: 1200px; height: 1200px; overflow: hidden; background: var(--page-bg); }
  .stage {
    width: 1200px; height: 1200px;
    display: flex; align-items: center; justify-content: center;
  }
  .wrap { display: flex; box-shadow: 0 20px 50px rgba(0,0,0,0.12); }
  .cover { width: 500px; height: 760px; background: var(--cover-white); display: block; }
  .spine {
    width: 56px; height: 760px;
    background: linear-gradient(90deg, #e4e4e4, #fafafa 40%, #e8e8e8);
  }
  .title-type { font-family: "Orbitron", sans-serif; font-weight: 800; }
  .body-type { font-family: "Outfit", sans-serif; }
</style>
</head>
<body>
<main class="stage">
  <div class="wrap">

    <!-- Back cover -->
    <svg class="cover back-cover" viewBox="0 0 500 760" xmlns="http://www.w3.org/2000/svg">
      <defs>
        <linearGradient id="portraitFill" x1="0" y1="0" x2="1" y2="1">
          <stop offset="0" stop-color="#7fb2d8"/>
          <stop offset="0.6" stop-color="#3d6fa6"/>
          <stop offset="1" stop-color="#1c2a4a"/>
        </linearGradient>
        <linearGradient id="decoFill" x1="0" y1="0" x2="1" y2="1">
          <stop offset="0" stop-color="#e9e6e5"/>
          <stop offset="0.6" stop-color="#e6dadd"/>
          <stop offset="1" stop-color="#e3c9cf"/>
        </linearGradient>
      </defs>
      <rect class="author-portrait" x="118" y="118" width="172" height="320" fill="url(#portraitFill)" role="img" aria-label="Author portrait in dress uniform in front of a flag"/>
      <text class="body-type back-blurb" x="304" y="136" font-size="14.5" fill="var(--ink)">
        <tspan x="304">It’s a biographical</tspan>
        <tspan x="304" dy="17">book about my life,</tspan>
        <tspan x="304" dy="17">including childhood</tspan>
        <tspan x="304" dy="17">trauma and my</tspan>
        <tspan x="304" dy="17">US Aerial Corps career.</tspan>
        <tspan x="304" dy="30">Its focus is on</tspan>
        <tspan x="304" dy="17">those serving in the</tspan>
        <tspan x="304" dy="17">military and post</tspan>
        <tspan x="304" dy="17">military life with</tspan>
        <tspan x="304" dy="17">an emphasis</tspan>
        <tspan x="304" dy="17">on trauma</tspan>
      </text>
      <text class="body-type back-author" x="304" y="474" font-size="23" fill="var(--crimson)">Wade Pemberton</text>
      <rect class="back-decoration" x="118" y="492" width="382" height="268" fill="url(#decoFill)" role="img" aria-label="Oversized title letter fragment in grey and crimson"/>
    </svg>

    <div class="spine"></div>

    <!-- Front cover -->
    <svg class="cover front-cover" viewBox="0 0 500 760" xmlns="http://www.w3.org/2000/svg">
      <defs>
        <linearGradient id="titleFill" x1="0" y1="0" x2="1" y2="1">
          <stop offset="0" stop-color="#6c645d"/>
          <stop offset="0.35" stop-color="#c23a52"/>
          <stop offset="0.55" stop-color="#6c645d"/>
          <stop offset="0.8" stop-color="#c23a52"/>
          <stop offset="1" stop-color="#5a7488"/>
        </linearGradient>
        <linearGradient id="sceneFill" x1="0" y1="0" x2="0" y2="1">
          <stop offset="0" stop-color="#a9b3bd"/>
          <stop offset="0.5" stop-color="#7f8792"/>
          <stop offset="0.85" stop-color="#3b3d42"/>
          <stop offset="1" stop-color="#141416"/>
        </linearGradient>
      </defs>

      <text class="body-type front-author" x="250" y="72" font-size="25" font-weight="500" text-anchor="middle" fill="var(--ink)">WADE PEMBERTON</text>

      <rect class="cover-scene" x="0" y="318" width="500" height="386" fill="url(#sceneFill)" role="img" aria-label="Fighter jet on the flightline at dusk with a lone figure walking, faint flag stars overhead"/>

      <text class="title-type title-row" x="34" y="196" font-size="118" textLength="432" lengthAdjust="spacingAndGlyphs" fill="url(#titleFill)">BOL</text>
      <text class="title-type title-row" x="34" y="310" font-size="118" textLength="130" lengthAdjust="spacingAndGlyphs" fill="url(#titleFill)">T</text>
      <text class="title-type title-amp" x="250" y="296" font-size="92" text-anchor="middle" fill="#231c1e">&amp;</text>
      <text class="title-type title-row" x="336" y="310" font-size="118" textLength="130" lengthAdjust="spacingAndGlyphs" fill="url(#titleFill)">S</text>

      <text class="title-type title-row-dark" x="34" y="446" font-size="118" textLength="432" lengthAdjust="spacingAndGlyphs" fill="var(--maroon)">BUR</text>
      <text class="title-type title-row-dark" x="34" y="568" font-size="112" textLength="432" lengthAdjust="spacingAndGlyphs" fill="var(--maroon)">DENS</text>

      <text class="body-type front-subtitle" x="250" y="740" font-size="26" font-weight="500" text-anchor="middle" fill="var(--crimson)">Mending What Lies Beneath</text>
    </svg>

  </div>
</main>
</body>
</html>
```